Business Card Design

We need a design for business cards for our company. We have a logo. We teach EMT's and we are based out of Virginia. The information that will need to add would be, name, title, phone number, email, address. On the back of the business card would be "Trained today, ready tomorrow"

Target Market(s)

People that want to become EMT's

Colors

Designer to choose colors to be used in the design.

Requirements
Must have
• company logo

```html
<!DOCTYPE html>
<html lang="en">
<head>
<meta charset="utf-8">
<title>Rescue Ready Academy – Business Card</title>
<link rel="stylesheet" href="https://fonts.googleapis.com/css2?family=Montserrat:wght@500;600&family=Roboto:wght@400&display=swap">
<style>
  :root {
    --backdrop: #2a2a2b;
    --card: #1e1f21;
    --pattern-top: #26272a;
    --pattern-bottom: #1e1f21;
    --brand-red: #d0202f;
    --text-grey: #c8c8c8;
    --muted-grey: #9a9a9a;
    --rule: #4a4b4e;
  }
  * { box-sizing: border-box; margin: 0; padding: 0; }
  html, body {
    width: 1200px; height: 1108px; overflow: hidden;
    background: var(--backdrop);
  }
  .sheet {
    position: relative; width: 1200px; height: 1108px;
    display: flex; justify-content: center; align-items: center; gap: 80px;
  }
  .card {
    position: relative; width: 400px; height: 686px;
    background: var(--card); border-radius: 22px; overflow: hidden;
    text-align: center;
  }
  /* Front */
  .brand {
    position: absolute; top: 150px; left: 0; right: 0;
    display: flex; align-items: center; justify-content: center; gap: 12px;
    font-family: "Montserrat", sans-serif; font-weight: 600;
    font-size: 24px; letter-spacing: -0.3px; color: var(--brand-red);
    text-transform: uppercase;
  }
  .brand-dot {
    width: 14px; height: 14px; border-radius: 50%; background: var(--brand-red);
    flex: none;
  }
  .contact {
    position: absolute; top: 430px; left: 0; right: 0;
    display: flex; flex-direction: column; align-items: center;
  }
  .person-name {
    font-family: "Montserrat", sans-serif; font-weight: 600;
    font-size: 22px; color: var(--brand-red); letter-spacing: -0.3px;
  }
  .person-title {
    font-family: "Roboto", sans-serif; font-size: 18px; color: var(--text-grey);
    margin-top: 2px;
  }
  .divider {
    width: 162px; height: 1px; background: var(--rule); margin: 12px 0;
  }
  .detail {
    font-family: "Roboto", sans-serif; font-size: 17px; line-height: 24px;
    color: var(--text-grey);
  }
  /* Back */
  .pattern-field {
    position: absolute; inset: 0 0 120px 0;
    background: linear-gradient(180deg, var(--pattern-top), var(--pattern-bottom));
  }
  .back-mark {
    position: absolute; top: 388px; left: 0; right: 0;
    display: flex; justify-content: center;
  }
  .back-mark .brand-dot { width: 22px; height: 22px; }
  .tagline {
    position: absolute; bottom: 64px; left: 0; right: 0;
    font-family: "Montserrat", sans-serif; font-weight: 600;
    font-size: 20px; letter-spacing: -0.3px; color: var(--muted-grey);
  }
</style>
</head>
<body>
  <main class="sheet">
    <section class="card card-front">
      <div class="brand"><span class="brand-dot"></span>Rescue Ready Academy</div>
      <div class="contact">
        <p class="person-name">DANIEL REEVES</p>
        <p class="person-title">Managing Director</p>
        <span class="divider"></span>
        <p class="detail">044-555 210 384</p>
        <p class="detail">hello@rescueready.example</p>
        <span class="divider"></span>
        <p class="detail">78 Harbor Lane, Suite 4</p>
        <p class="detail">23219, Virginia</p>
      </div>
    </section>
    <section class="card card-back">
      <div class="pattern-field" role="img" aria-label="Faint repeating pattern of the brand symbol"></div>
      <div class="back-mark"><span class="brand-dot"></span></div>
      <p class="tagline">TRAINED TODAY, READY TOMORROW</p>
    </section>
  </main>
</body>
</html>
```